Brightfen Business Card Redesign & Logo Update

We need to update our business cards to something more modern and fresh. Brightfen can provide the current color schemes and old design examples, but welcome creativity in helping us with this redesign. PLEASE NOTE that we no longer utilize the "tree" and/or "leaf" imagery in our branding. If able would apprecaite an update on the quality of our "words only" logo in Ai. / PNG formats too.

Target Market(s)

Investors, landowners, corporate partners, contractors

Industry/Entity Type

Environmental Restoration & Conservation

Contact Information for Business Card

Logo, persons name, title, mailing address, phone and email, website url

Font styles to use
Other font styles liked:
• Merriweather

Requirements
Nice to have
• Logo, persons name, title, mailing address, phone and email, website url, but open to ideams
Should not have
• No all back backgrounds

```html
<!DOCTYPE html>
<html lang="en">
<head>
<meta charset="utf-8">
<title>Brightfen Business Card</title>
<link rel="stylesheet" href="https://fonts.googleapis.com/css2?family=Open+Sans:wght@400;600;700;800&display=swap">
<style>
  :root {
    --stage: #2b2b2d;
    --orange: #ec8025;
    --green: #12823f;
    --ink: #1b1b1c;
    --band: #232325;
    --paper: #ffffff;
  }
  * { margin: 0; padding: 0; box-sizing: border-box; }
  html, body { width: 1200px; height: 780px; overflow: hidden; }
  body {
    background: var(--stage);
    font-family: "Open Sans", Arial, sans-serif;
    position: relative;
  }
  .card {
    position: absolute;
    width: 540px;
    height: 309px;
    overflow: hidden;
    box-shadow: 0 10px 24px rgba(0,0,0,.45);
  }

  /* Front */
  .card-front {
    left: 40px; top: 70px;
    background: var(--orange);
    display: flex; flex-direction: column;
    align-items: center; justify-content: center;
  }
  .brand-name {
    font-weight: 800;
    font-size: 74px;
    letter-spacing: 1px;
    line-height: 1;
    color: var(--paper);
    text-transform: uppercase;
  }
  .brand-descriptor {
    margin-top: 8px;
    font-weight: 800;
    font-size: 21px;
    letter-spacing: .5px;
    color: var(--ink);
    text-transform: uppercase;
  }

  /* Back */
  .card-back {
    left: 620px; top: 400px;
    background: var(--paper);
    display: flex;
  }
  .brand-band {
    width: 180px;
    height: 100%;
    background: var(--band);
    position: relative;
  }
  .brand-band-lockup {
    position: absolute;
    left: 50%; top: 50%;
    width: 280px;
    transform: translate(-50%, -50%) rotate(-90deg);
    text-align: center;
  }
  .brand-band-name {
    font-weight: 800;
    font-size: 44px;
    line-height: 1;
    color: var(--orange);
    text-transform: uppercase;
  }
  .brand-band-descriptor {
    margin-top: 6px;
    font-weight: 700;
    font-size: 12.5px;
    letter-spacing: .4px;
    color: var(--paper);
    text-transform: uppercase;
  }

  .details {
    flex: 1;
    padding: 30px 28px 0 34px;
  }
  .identity {
    border-top: 1.5px solid var(--ink);
    border-bottom: 1.5px solid var(--ink);
    padding: 20px 0 16px;
  }
  .person-name {
    font-weight: 700;
    font-size: 25px;
    line-height: 1.1;
  }
  .person-first { color: var(--orange); }
  .person-last { color: var(--green); }
  .person-title {
    font-size: 14px;
    color: var(--ink);
    margin-top: 3px;
  }
  .address {
    margin-top: 36px;
    font-size: 13px;
    line-height: 1.45;
    color: var(--ink);
  }
  .contact-list {
    list-style: none;
    margin-top: 8px;
    font-size: 13px;
    line-height: 1.5;
    color: var(--ink);
  }
  .contact-list li { display: flex; align-items: center; gap: 8px; }
  .contact-icon { width: 13px; height: 13px; flex: none; }
</style>
</head>
<body>

  <section class="card card-front" aria-label="Business card front">
    <div class="brand-name">Brightfen</div>
    <div class="brand-descriptor">Environmental Credit Company</div>
  </section>

  <section class="card card-back" aria-label="Business card back">
    <div class="brand-band">
      <div class="brand-band-lockup">
        <div class="brand-band-name">Brightfen</div>
        <div class="brand-band-descriptor">Environmental Credit Company</div>
      </div>
    </div>

    <div class="details">
      <div class="identity">
        <div class="person-name"><span class="person-first">Marta</span> <span class="person-last">Kolarova</span></div>
        <div class="person-title">Managing Director</div>
      </div>

      <address class="address" style="font-style:normal">
        1840 Meadowlark Ave. Suite 310<br>
        Fort Worth, TX 76104
      </address>

      <ul class="contact-list">
        <li>
          <svg class="contact-icon" viewBox="0 0 24 24" aria-hidden="true">
            <path fill="#ec8025" d="M6.6 10.8a15.2 15.2 0 0 0 6.6 6.6l2.2-2.2c.3-.3.7-.4 1-.2 1.1.4 2.3.6 3.6.6.6 0 1 .4 1 1V20c0 .6-.4 1-1 1A17 17 0 0 1 3 4c0-.6.4-1 1-1h3.5c.6 0 1 .4 1 1 0 1.3.2 2.5.6 3.6.1.3 0 .7-.2 1z"/>
          </svg>
          (817) 555-0143
        </li>
        <li>
          <svg class="contact-icon" viewBox="0 0 24 24" aria-hidden="true">
            <rect x="2" y="5" width="20" height="14" rx="1.5" fill="#ec8025"/>
            <path d="M3 6.5l9 6.5 9-6.5" fill="none" stroke="#fff" stroke-width="1.8"/>
          </svg>
          info@brightfen.com
        </li>
        <li>
          <svg class="contact-icon" viewBox="0 0 24 24" aria-hidden="true">
            <circle cx="12" cy="12" r="10" fill="#ec8025"/>
            <path d="M2 12h20M12 2c3 3 3 17 0 20M12 2c-3 3-3 17 0 20" fill="none" stroke="#fff" stroke-width="1.4"/>
          </svg>
          www.brightfen.com
        </li>
      </ul>
    </div>
  </section>

</body>
</html>
```